Stationary Set Rebrand for Brennick

We are a Canadian Distribution and Service Company that was established in 1969. Over the past 5 decades we have expanded our business and have warehouses across Canada. We specialize in adhesive tapes, adhesives, films, safety, warehouse, shipping, janitorial and packaging supplies.

We have updated our logo design and would like a new corporate branding identity that includes a new fresh Stationary Set (Business Cards, Letterhead, Letterhead MS Word, Envelope, Presentation Folders, Email Signatures, Notepad Covers, etc.)

Target Market(s)

Industrial Business Sector

Font styles to use
Sans Serif

Colors
0054AA
0677BA
7BADD7
CADEEF
E8F1F8
0094D4
00A9DD
6FCCEA
C7EBF8
E9F6FB
00AB8E
00BBA5
67D7C9
C6EFE9
E9F9F6
EB3D1F
EC4F4E
F09395
F8D3D4
FCEDEE

Requirements
Should not have
• Colors not too light, darker colours preferred

```html
<!DOCTYPE html>
<html lang="en">
<head>
<meta charset="utf-8">
<title>Brennick Business Card</title>
<link href="https://fonts.googleapis.com/css2?family=Saira:wght@400;700;800&display=swap" rel="stylesheet">
<style>
  :root {
    --brand-red: #d71920;
    --ink: #1d1a1b;
    --text-grey: #4a4a4a;
    --muted-grey: #6b6b6b;
    --paper: #ffffff;
    --backdrop: #dcdcdc;
  }
  * { margin: 0; padding: 0; box-sizing: border-box; }
  html, body {
    width: 1200px;
    height: 1200px;
    overflow: hidden;
    background: var(--backdrop);
    font-family: "Saira", sans-serif;
  }
  .card {
    position: absolute;
    left: 252px;
    width: 696px;
    height: 398px;
  }
  .card-front { top: 156px; background: var(--paper); }
  .card-back { top: 651px; background: var(--brand-red); }

  .holder-name {
    position: absolute;
    left: 38px;
    top: 48px;
    font-size: 26px;
    font-weight: 700;
    letter-spacing: 1px;
    color: var(--brand-red);
    line-height: 1;
    text-transform: uppercase;
  }
  .holder-title {
    position: absolute;
    left: 38px;
    top: 76px;
    font-size: 15px;
    color: var(--muted-grey);
    letter-spacing: 0.5px;
    line-height: 1;
  }
  .address {
    position: absolute;
    left: 38px;
    top: 114px;
    font-size: 16px;
    color: var(--text-grey);
    line-height: 21px;
    letter-spacing: 0.4px;
  }
  .contact-list {
    position: absolute;
    left: 38px;
    top: 168px;
    list-style: none;
  }
  .contact-item {
    display: flex;
    align-items: center;
    height: 20.7px;
    font-size: 16px;
    color: var(--text-grey);
    letter-spacing: 0.4px;
  }
  .contact-icon {
    width: 14px;
    height: 14px;
    margin-right: 13px;
    fill: var(--brand-red);
    flex: none;
  }
  .wordmark-front {
    position: absolute;
    left: 36px;
    top: 268px;
    font-size: 60px;
    font-weight: 800;
    color: var(--ink);
    line-height: 1;
  }
  .brand-symbol-area {
    position: absolute;
    left: 375px;
    top: 70px;
    width: 260px;
    height: 260px;
    border-radius: 50%;
    background: var(--brand-red);
  }
  .wordmark-back {
    position: absolute;
    left: 0;
    right: 0;
    top: 140px;
    text-align: center;
    font-size: 100px;
    font-weight: 800;
    color: var(--paper);
    line-height: 1;
  }
</style>
</head>
<body>
  <section class="card card-front">
    <h1 class="holder-name">Dana Whitfield</h1>
    <p class="holder-title">President</p>
    <p class="address">4210 Cedarbrook Road<br>Halton, Canada 58210</p>
    <ul class="contact-list">
      <li class="contact-item">
        <svg class="contact-icon" viewBox="0 0 24 24"><path d="M6.6 10.8a15.1 15.1 0 0 0 6.6 6.6l2.2-2.2a1 1 0 0 1 1-.25 11.4 11.4 0 0 0 3.6.57 1 1 0 0 1 1 1V20a1 1 0 0 1-1 1A17 17 0 0 1 3 4a1 1 0 0 1 1-1h3.5a1 1 0 0 1 1 1c0 1.25.2 2.45.57 3.57a1 1 0 0 1-.25 1z"/></svg>
        555-214-0187
      </li>
      <li class="contact-item">
        <svg class="contact-icon" viewBox="0 0 24 24"><path d="M7 1h10a2 2 0 0 1 2 2v18a2 2 0 0 1-2 2H7a2 2 0 0 1-2-2V3a2 2 0 0 1 2-2zm0 3v14h10V4zm5 15.5a1 1 0 1 0 0 2 1 1 0 0 0 0-2z"/></svg>
        555-318-6620
      </li>
      <li class="contact-item">
        <svg class="contact-icon" viewBox="0 0 24 24"><path d="M2 5h20v14H2zm2 2v.5l8 5.5 8-5.5V7l-8 5.5z"/></svg>
        info@brennick.com
      </li>
      <li class="contact-item">
        <svg class="contact-icon" viewBox="0 0 24 24"><circle cx="12" cy="12" r="10"/></svg>
        www.brennick.com
      </li>
    </ul>
    <div class="wordmark-front">Brennick</div>
    <div class="brand-symbol-area" role="img" aria-label="Brand symbol decoration area"></div>
  </section>

  <section class="card card-back">
    <div class="wordmark-back">Brennick</div>
  </section>
</body>
</html>
```